Business Card for premium dental clinic

We are a premium dental clinic based in Brasov, Romania with more than 15 year on the market, providing quality dental treatment made by a team of more specialized dentists, working with modern equipment as a solution to beautiful and healthy teeth.

Our current logo for the clinic use 2 square with colors black and gold - dr Ternisu - studio, using family fonts Bodoni, Myriad Pro and Segoe Print.
Depending on the printing we used some gold CMYK background or gold foil picture background or a gold gradient.
We want a business card:
- eye catching business card
- distinguished business card
- premium design
- to keep the color scheme of black and gold
- to attract the customers to spent time reading the information
- modern concept

```html
<!DOCTYPE html>
<html lang="en">
<head>
<meta charset="utf-8">
<title>dr Ternisu studio – business card</title>
<link rel="stylesheet" href="https://fonts.googleapis.com/css2?family=Source+Sans+3:wght@400;600&display=swap">
<style>
  :root {
    --backdrop: #d9d9d9;
    --card-black: #060606;
    --gold-light: #f7e27a;
    --gold-mid: #d9a42a;
    --gold-deep: #9c6a12;
    --text-white: #ffffff;
  }
  * { margin: 0; padding: 0; box-sizing: border-box; }
  html, body {
    width: 1200px; height: 1006px; overflow: hidden;
    background: var(--backdrop);
    font-family: "Source Sans 3", "Myriad Pro", sans-serif;
  }
  .business-card {
    position: absolute;
    left: 100px; top: 218px;
    width: 1000px; height: 570px;
    padding: 22px;
    background: linear-gradient(110deg, var(--gold-deep) 0%, var(--gold-mid) 22%, var(--gold-light) 45%, var(--gold-mid) 65%, var(--gold-deep) 85%, var(--gold-mid) 100%);
    box-shadow: 0 10px 30px rgba(0,0,0,.25);
  }
  .card-face {
    position: relative;
    width: 100%; height: 100%;
    background: var(--card-black);
    color: var(--text-white);
  }
  .brand-block {
    position: absolute;
    left: 196px; top: 100px;
    width: 470px; height: 240px;
    border: 2px solid var(--text-white);
    display: flex; align-items: center;
  }
  .brand-swatch {
    width: 236px; height: 100%;
    background: linear-gradient(135deg, var(--gold-light), var(--gold-mid) 55%, var(--gold-deep));
  }
  .brand-name {
    flex: 1;
    text-align: center;
    font-size: 40px;
    font-weight: 400;
    line-height: 1.15;
    color: var(--text-white);
  }
  .contact-details {
    position: absolute;
    left: 196px; top: 372px;
    width: 520px;
    font-size: 24px;
    line-height: 1.3;
    color: var(--text-white);
  }
  .contact-columns { display: flex; justify-content: space-between; }
  .contact-line { display: flex; align-items: center; gap: 10px; }
  .contact-line svg { width: 20px; height: 20px; flex: none; }
  .postal-address { margin-top: 16px; }
</style>
</head>
<body>
  <div class="business-card">
    <div class="card-face">
      <div class="brand-block">
        <div class="brand-swatch" role="img" aria-label="Gold foil texture"></div>
        <div class="brand-name">dr Ternisu<br>studio</div>
      </div>

      <div class="contact-details">
        <div class="contact-columns">
          <div class="phone-list">
            <div class="contact-line">
              <svg viewBox="0 0 20 20" aria-hidden="true"><rect x="5" y="1.5" width="10" height="17" rx="2" fill="none" stroke="#d9a42a" stroke-width="2"/><circle cx="10" cy="15.5" r="1" fill="#d9a42a"/></svg>
              <span>+40 700 318 452</span>
            </div>
            <div class="contact-line">
              <svg viewBox="0 0 20 20" aria-hidden="true"><path d="M4 2l3 0 2 5-2 1.5c1 2.2 2.5 3.7 4.5 4.5L13 11l5 2v3c0 1-1 2-2 2C8.5 18 2 11.5 2 4c0-1 1-2 2-2z" fill="#d9a42a"/></svg>
              <span>+40 268 500 916</span>
            </div>
          </div>
          <div class="web-list">
            <div class="contact-line">
              <svg viewBox="0 0 20 20" aria-hidden="true"><rect x="1.5" y="4" width="17" height="12" fill="none" stroke="#d9a42a" stroke-width="2"/><path d="M1.5 4l8.5 7 8.5-7" fill="none" stroke="#d9a42a" stroke-width="2"/></svg>
              <span>info@drternisu.ro</span>
            </div>
            <div class="contact-line">
              <svg viewBox="0 0 20 20" aria-hidden="true"><g fill="none" stroke="#d9a42a" stroke-width="1.6"><circle cx="10" cy="10" r="8"/><ellipse cx="10" cy="10" rx="3.5" ry="8"/><path d="M2 10h16M3.5 5.5h13M3.5 14.5h13"/></g></svg>
              <span>www.drternisu.ro</span>
            </div>
          </div>
        </div>
        <div class="postal-address">strada Lunga nr 8, Brasov, Romania 500120</div>
      </div>
    </div>
  </div>
</body>
</html>
```